Voranta Imports Busisness cards and logo

Voranta imports is a brand new wholesale company located in Londonderry, New Hampshire dedicated to finding unique products from around the world.
Licensed to sell wine and spirits in the state and also authorized distributors of Pale Meadow Design, a manufacturer of girls and women shoes. Other products that we are currently trying to import are cheese and frozen food from Spain.
We would like a design that portraits our diversity of products and wholesale capabilities

```html
<!DOCTYPE html>
<html lang="en">
<head>
<meta charset="utf-8">
<title>Voranta Imports – Business Card</title>
<link href="https://fonts.googleapis.com/css2?family=Exo+2:wght@400;500;700&display=swap" rel="stylesheet">
<style>
  :root {
    --backdrop: #2f3032;
    --card: #ffffff;
    --green-dark: #1b6a16;
    --green: #2e8b1f;
    --green-light: #6cc431;
    --lime: #8fd43c;
    --ink: #2b2b2b;
    --divider: #7a7a7a;
  }
  * { box-sizing: border-box; margin: 0; padding: 0; }
  html, body { width: 1200px; height: 817px; overflow: hidden; }
  body {
    background: var(--backdrop);
    font-family: "Exo 2", "Trebuchet MS", sans-serif;
    position: relative;
  }
  .business-card {
    position: absolute;
    left: 110px; top: 128px;
    width: 980px; height: 560px;
    background: var(--card);
    border-radius: 44px;
    overflow: hidden;
  }
  .brand {
    position: absolute;
    left: 0; right: 0; top: 62px;
    display: flex; align-items: center; justify-content: center;
    gap: 22px;
  }
  .brand-mark {
    width: 86px; height: 86px; border-radius: 50%;
    background: var(--green-light);
  }
  .brand-name {
    font-size: 58px; font-weight: 700; color: var(--green);
    letter-spacing: 0.5px;
  }
  .name-band {
    position: absolute; left: 0; right: 0; top: 196px; height: 58px;
    background: linear-gradient(90deg, var(--green-dark), var(--green) 60%, var(--green-dark));
    display: flex; align-items: center; padding-left: 54px; gap: 18px;
    color: #fff;
  }
  .name-band svg { width: 34px; height: 34px; }
  .person-name { font-size: 30px; font-weight: 500; letter-spacing: 1.5px; text-transform: uppercase; }
  .sep { width: 2px; height: 28px; background: #fff; }
  .person-role { font-size: 19px; letter-spacing: 1.5px; text-transform: uppercase; }
  .contacts {
    position: absolute; left: 40px; right: 40px; top: 282px; height: 170px;
    display: flex; align-items: center;
  }
  .contact {
    flex: 1 1 0; min-width: 0; height: 100%;
    padding: 0 18px;
    display: flex; flex-direction: column; align-items: center; justify-content: center; gap: 20px;
    position: relative;
  }
  .contact + .contact::before {
    content: ""; position: absolute; left: 0; top: 22px; bottom: 22px;
    width: 3px; background: var(--divider);
  }
  .icon-dot {
    width: 72px; height: 72px; border-radius: 50%;
    background: radial-gradient(circle at 40% 35%, var(--lime), var(--green) 80%);
    display: flex; align-items: center; justify-content: center;
  }
  .icon-dot svg { width: 38px; height: 38px; }
  .contact-text { font-size: 22px; color: var(--ink); letter-spacing: 0.8px; white-space: nowrap; }
  .address-band {
    position: absolute; left: 0; right: 0; bottom: 44px; height: 50px;
    background: linear-gradient(90deg, var(--green-dark), var(--green) 55%, var(--green-light));
    display: flex; align-items: center; padding-left: 50px; gap: 16px;
    color: #fff; font-size: 21px; letter-spacing: 2px;
  }
  .address-band svg { width: 24px; height: 30px; }
</style>
</head>
<body>
  <main class="business-card">
    <header class="brand">
      <span class="brand-mark"></span>
      <span class="brand-name">Voranta Imports</span>
    </header>

    <div class="name-band">
      <svg viewBox="0 0 34 34" aria-hidden="true"><circle cx="17" cy="10" r="8" fill="#fff"/><path d="M2 34c0-9 7-14 15-14s15 5 15 14z" fill="#fff"/></svg>
      <span class="person-name">Daniel Marlowe</span>
      <span class="sep"></span>
      <span class="person-role">General Manager</span>
    </div>

    <section class="contacts">
      <div class="contact phone">
        <span class="icon-dot"><svg viewBox="0 0 38 38" aria-hidden="true"><rect x="11" y="3" width="16" height="32" rx="3" fill="none" stroke="#fff" stroke-width="2.5"/><rect x="14" y="8" width="10" height="19" fill="#fff"/><circle cx="19" cy="31" r="1.6" fill="#fff"/></svg></span>
        <span class="contact-text">603 555 0147</span>
      </div>
      <div class="contact email">
        <span class="icon-dot"><svg viewBox="0 0 38 38" aria-hidden="true"><rect x="4" y="9" width="30" height="20" fill="#fff"/><path d="M4 9l15 12 15-12" fill="none" stroke="#2e8b1f" stroke-width="2"/></svg></span>
        <span class="contact-text">hello@voranta.com</span>
      </div>
      <div class="contact web">
        <span class="icon-dot"><svg viewBox="0 0 38 38" aria-hidden="true" fill="none" stroke="#fff" stroke-width="2"><circle cx="19" cy="19" r="14"/><ellipse cx="19" cy="19" rx="6" ry="14"/><path d="M5 19h28M8 11h22M8 27h22M19 5v28"/></svg></span>
        <span class="contact-text">www.vorantaimports.com</span>
      </div>
    </section>

    <footer class="address-band">
      <svg viewBox="0 0 24 30" aria-hidden="true"><path d="M12 1C6 1 2 5.5 2 11c0 7 10 18 10 18s10-11 10-18C22 5.5 18 1 12 1z" fill="#fff"/><circle cx="12" cy="11" r="4" fill="#2e8b1f"/></svg>
      <span class="address">27 Harbor Lane, Suite 4, Londonderry NH</span>
    </footer>
  </main>
</body>
</html>
```